Specialised investor in e-mobility and energy wants business card design

We need a business card design that fits our existing corporate design. <The look and feel must be 'sharp'/'clean', dynamic, communicate momentum, professionalism etc (as one would imagine from a firm in the financial sector). We like the idea of a reverse-side of the card that includes the logo, and the name and contact details on the other. We expect the deliverable to be whatever format might be required to be able to get cards printed directly by a service such as kelmo press. Our website is www.zub.capital

```html
<!DOCTYPE html>
<html lang="en">
<head>
<meta charset="utf-8">
<title>Zub Capital – Business Card</title>
<link href="https://fonts.googleapis.com/css2?family=Montserrat:wght@400;500;700&display=swap" rel="stylesheet">
<style>
  :root {
    --green-dark: #3b5a2a;
    --green-light: #8dbf4e;
    --ink: #2b2b2b;
    --card: #ffffff;
    --backdrop: #e9ebe6;
  }
  * { margin: 0; padding: 0; box-sizing: border-box; }
  html, body { width: 1200px; height: 960px; overflow: hidden; }
  body {
    background: var(--backdrop);
    font-family: "Montserrat", Arial, sans-serif;
    position: relative;
  }
  .card {
    position: absolute;
    left: 290px;
    width: 620px;
    height: 360px;
    background: var(--card);
    border-radius: 30px;
    box-shadow: 0 6px 18px rgba(0,0,0,0.12);
    overflow: hidden;
  }
  .card--back { top: 50px; }
  .card--front { top: 500px; }

  .wordmark {
    color: var(--green-dark);
    font-weight: 500;
    letter-spacing: 0.5px;
    white-space: nowrap;
  }
  .card--back .wordmark {
    position: absolute;
    left: 0; right: 0; top: 140px;
    text-align: center;
    font-size: 64px;
  }
  .card--front .wordmark--small {
    position: absolute;
    left: 36px; top: 38px;
    font-size: 30px;
  }
  .card--front .wordmark--large {
    position: absolute;
    left: 36px; top: 110px;
    font-size: 52px;
  }

  .identity {
    position: absolute;
    right: 0; top: 44px;
    text-align: right;
  }
  .identity__row { display: flex; align-items: center; justify-content: flex-end; }
  .identity__name {
    color: var(--green-light);
    font-weight: 700;
    font-size: 22px;
    letter-spacing: 0.5px;
    margin-right: 10px;
  }
  .identity__bar { width: 22px; height: 34px; background: var(--green-light); }
  .identity__title {
    color: var(--ink);
    font-size: 14px;
    margin-right: 32px;
    margin-top: 2px;
  }

  .office {
    position: absolute;
    right: 32px; bottom: 40px;
    text-align: right;
    font-size: 16px;
    line-height: 1.45;
  }
  .office__company { color: var(--green-light); font-weight: 500; }
  .office__city { color: var(--ink); }

  .contacts {
    position: absolute;
    left: 40px; bottom: 34px;
    list-style: none;
    font-size: 16px;
    color: var(--ink);
    line-height: 1.55;
  }
  .contacts li { display: flex; align-items: center; gap: 10px; }
  .contacts svg { width: 14px; height: 14px; fill: var(--green-light); flex: none; }
</style>
</head>
<body>
  <section class="card card--back">
    <div class="wordmark">Zub Capital</div>
  </section>

  <section class="card card--front">
    <div class="wordmark wordmark--small">Zub Capital</div>
    <div class="wordmark wordmark--large">Zub Capital</div>

    <div class="identity">
      <div class="identity__row">
        <span class="identity__name">ELIAS VARDEN</span>
        <span class="identity__bar"></span>
      </div>
      <div class="identity__title">Managing Director</div>
    </div>

    <div class="office">
      <div class="office__company">Zub Capital S.A.</div>
      <div class="office__city">Marenvale, Alvoria</div>
    </div>

    <ul class="contacts">
      <li>
        <svg viewBox="0 0 16 16" aria-hidden="true"><path d="M3 1h3l1.5 4-2 1.2a9 9 0 0 0 4.3 4.3L11 8.5l4 1.5v3a2 2 0 0 1-2 2A13 13 0 0 1 1 3a2 2 0 0 1 2-2z"/></svg>
        +41 79 555 0142
      </li>
      <li>
        <svg viewBox="0 0 16 16" aria-hidden="true"><path d="M1 3h14v10H1z M1 3l7 6 7-6" fill="var(--green-light)" stroke="#fff" stroke-width="1.2"/></svg>
        elias@zub.capital
      </li>
      <li>
        <svg viewBox="0 0 16 16" aria-hidden="true"><circle cx="8" cy="8" r="7"/><path d="M1 8h14M8 1c3 3 3 11 0 14M8 1c-3 3-3 11 0 14" fill="none" stroke="#fff" stroke-width="1"/></svg>
        www.zub.capital
      </li>
    </ul>
  </section>
</body>
</html>
```